Business card design for Brivo Engineering Tandem

We need a new business card design along with all the necessary to place an order. The company is Brivo Engineering Tandem and we recently updated our logo.

```html
<!DOCTYPE html>
<html lang="en">
<head>
<meta charset="utf-8">
<title>Brivo Engineering Tandem – Business Card</title>
<link rel="stylesheet" href="https://fonts.googleapis.com/css2?family=Montserrat:wght@400;500;700&display=swap">
<style>
  :root {
    --bg: #d3d8d8;
    --paper: #f1f1ef;
    --yellow: #e9c21f;
    --grey: #8f8f8f;
    --ink: #2f2f2f;
  }
  * { box-sizing: border-box; margin: 0; padding: 0; }
  html, body { width: 1200px; height: 881px; overflow: hidden; }
  body {
    background: var(--bg);
    font-family: "Montserrat", sans-serif;
    display: flex;
    align-items: center;
    justify-content: center;
    gap: 40px;
  }
  .card {
    width: 540px;
    height: 309px;
    background: var(--paper);
    border-bottom: 5px solid var(--yellow);
    box-shadow: 0 10px 24px rgba(0,0,0,0.12);
    position: relative;
  }
  /* contact side */
  .card--contact {
    display: flex;
    align-items: center;
    justify-content: center;
    gap: 26px;
  }
  .identity { text-align: right; }
  .identity__name {
    color: var(--yellow);
    font-weight: 700;
    font-size: 22px;
    letter-spacing: 0.5px;
  }
  .identity__role {
    color: var(--ink);
    font-size: 14px;
    margin-top: 4px;
  }
  .divider {
    width: 2px;
    height: 64px;
    background: var(--yellow);
  }
  .contacts { list-style: none; }
  .contacts li {
    display: flex;
    align-items: center;
    gap: 8px;
    color: var(--ink);
    font-size: 14px;
    line-height: 22px;
  }
  .contacts svg { width: 12px; height: 12px; fill: var(--yellow); flex: none; }
  /* brand side */
  .card--brand {
    display: flex;
    align-items: center;
    justify-content: center;
    gap: 14px;
  }
  .brand__mark {
    width: 22px; height: 22px;
    background: var(--yellow);
  }
  .brand__name {
    color: var(--grey);
    font-weight: 700;
    font-size: 28px;
    line-height: 1.15;
    letter-spacing: 1px;
    text-transform: uppercase;
  }
</style>
</head>
<body>
  <section class="card card--contact">
    <div class="identity">
      <p class="identity__name">DANIEL HART</p>
      <p class="identity__role">Managing Director</p>
    </div>
    <div class="divider"></div>
    <ul class="contacts">
      <li>
        <svg viewBox="0 0 24 24"><path d="M6.6 10.8a15 15 0 0 0 6.6 6.6l2.2-2.2a1 1 0 0 1 1-.25 11.4 11.4 0 0 0 3.6.6 1 1 0 0 1 1 1V20a1 1 0 0 1-1 1A17 17 0 0 1 3 4a1 1 0 0 1 1-1h3.5a1 1 0 0 1 1 1c0 1.25.2 2.45.6 3.6a1 1 0 0 1-.25 1z"/></svg>
        555 210 384
      </li>
      <li>
        <svg viewBox="0 0 24 24"><path d="M2 5h20v14H2z M2 5l10 8 10-8" fill="none" stroke="#e9c21f" stroke-width="2.5"/></svg>
        hello@brivotandem.com
      </li>
      <li>
        <svg viewBox="0 0 24 24"><circle cx="12" cy="12" r="10"/></svg>
        www.brivotandem.com
      </li>
    </ul>
  </section>

  <section class="card card--brand">
    <span class="brand__mark"></span>
    <p class="brand__name">Brivo Engineering<br>Tandem</p>
  </section>
</body>
</html>
```